New Business Card Design Project

Use the flyer uploaded and website www.brightoakbuilders.com for inspiration.
List Our Services on Backside of business cards
Marcus Delling
Harborline Builders Inc.
Licensed General Contractors
858-471-6093

Contact Information for Business Card

Use the flyer uploaded and website www.brightoakbuilders.com for inspiration. List Our Services on Backside of business cards Marcus Delling Harborline Builders Inc. Licensed General Contractors 858-471-6093

```html
<!DOCTYPE html>
<html lang="en">
<head>
<meta charset="utf-8">
<title>Harborline Builders – Business Cards</title>
<link href="https://fonts.googleapis.com/css2?family=Oswald:wght@600&family=Open+Sans:wght@400;600&display=swap" rel="stylesheet">
<style>
  :root {
    --bg: #c9c9c9;
    --ink: #121212;
    --blue: #3581c6;
    --red: #e3101b;
    --white: #ffffff;
    --photo-a: #d9dadb;
    --photo-b: #9fa3a6;
    --photo-c: #e2b58a;
    --photo-d: #f1ece4;
  }
  * { box-sizing: border-box; margin: 0; padding: 0; }
  html, body { width: 1200px; height: 800px; overflow: hidden; }
  body {
    background: radial-gradient(circle at 70% 20%, #dedede, var(--bg) 70%);
    font-family: "Open Sans", sans-serif;
    position: relative;
  }
  .card {
    position: absolute;
    left: 300px;
    width: 600px;
    height: 343px;
    border-radius: 18px;
    overflow: hidden;
    background: var(--white);
    box-shadow: 0 8px 24px rgba(0,0,0,.25);
    border-bottom: 3px solid var(--blue);
  }
  .card--front { top: 32px; }
  .card--back { top: 420px; }

  .card__top {
    position: absolute; left: 0; top: 0; width: 100%; height: 120px;
    background: var(--ink);
  }
  .brand {
    position: absolute; right: 28px; top: 40px;
    display: flex; align-items: center; gap: 10px;
  }
  .brand__mark { width: 12px; height: 12px; background: var(--white); }
  .brand__name {
    color: var(--white); font-weight: 400; font-size: 19px; letter-spacing: 2px;
    font-family: "Open Sans", sans-serif;
  }
  .holder-name {
    position: absolute; left: 34px; top: 52px;
    font-family: "Oswald", sans-serif; font-weight: 600; font-size: 40px;
    color: var(--red); text-transform: uppercase; letter-spacing: .5px;
  }
  .guarantee {
    position: absolute; left: 34px; top: 56px;
    font-family: "Oswald", sans-serif; font-weight: 600; font-size: 28px;
    color: var(--red); text-transform: uppercase;
  }
  .panel {
    position: absolute; left: 0; top: 130px; width: 300px; height: 152px;
    background: var(--blue); color: var(--white);
  }
  .photo {
    position: absolute; left: 300px; top: 126px; right: 0; height: 160px;
  }
  .card--front .photo { background: linear-gradient(135deg, var(--photo-d), var(--photo-a) 45%, var(--photo-b)); }
  .card--back .photo { background: linear-gradient(135deg, var(--photo-d), var(--photo-c) 55%, #c98a55); }

  .contact-list { list-style: none; padding: 34px 0 0 34px; }
  .contact-list li {
    display: flex; align-items: center; gap: 10px;
    font-size: 17px; line-height: 28px;
  }
  .contact-list svg { width: 16px; height: 16px; flex: none; }

  .company {
    position: absolute; left: 34px; top: 288px;
    color: var(--red); font-size: 17px; line-height: 22px; font-weight: 600;
  }

  .service-list { list-style: none; padding: 8px 0 0 24px; }
  .service-list li {
    font-size: 13.5px; line-height: 15.5px; display: flex; align-items: center; gap: 8px;
  }
  .service-list li::before {
    content: ""; width: 6px; height: 6px; border-radius: 50%; background: var(--red); flex: none;
  }
  .card--back .panel { top: 126px; height: 190px; }
  .card--back .photo { height: 185px; }
</style>
</head>
<body>

<section class="card card--front">
  <div class="card__top"></div>
  <h1 class="holder-name">Marcus Delling</h1>
  <div class="brand"><span class="brand__mark"></span><span class="brand__name">HARBORLINE BUILDERS</span></div>
  <div class="panel">
    <ul class="contact-list">
      <li><svg viewBox="0 0 16 16"><path d="M4 1l3 3-2 2c1 2 3 4 5 5l2-2 3 3-2 3C7 14 2 9 1 4z" fill="#fff"/></svg>858-471-6093</li>
      <li><svg viewBox="0 0 16 16"><rect x="1" y="3" width="14" height="10" fill="#fff"/><path d="M1 3l7 6 7-6" stroke="#3581c6" stroke-width="1.5" fill="none"/></svg>info@harborlinebuilders.com</li>
      <li><svg viewBox="0 0 16 16"><circle cx="8" cy="8" r="7" fill="#fff"/><path d="M1 8h14M8 1v14M3 4h10M3 12h10" stroke="#3581c6" stroke-width="1"/><ellipse cx="8" cy="8" rx="3" ry="7" stroke="#3581c6" fill="none"/></svg>www.brightoakbuilders.com</li>
    </ul>
  </div>
  <div class="photo" role="img" aria-label="Photo of a bright remodeled white kitchen interior"></div>
  <p class="company">Harborline Builders Inc.<br>Licensed General Contractors</p>
</section>

<section class="card card--back">
  <div class="card__top"></div>
  <p class="guarantee">100% Guarenteed</p>
  <div class="brand"><span class="brand__mark"></span><span class="brand__name">HARBORLINE BUILDERS</span></div>
  <div class="panel">
    <ul class="service-list">
      <li>Remodel: Kitchen &amp; Bath</li>
      <li>Painting: Interior &amp; Exterior</li>
      <li>Flooring: Carpet, Vinyl, Wood</li>
      <li>Window &amp; Door Replacement</li>
      <li>Plumbing: Repairs &amp; Upgrades</li>
      <li>Energy-Efficient Upgrades</li>
      <li>Deck &amp; Patio Construction</li>
      <li>Water &amp; Mold Damage</li>
      <li>Garage Renovation</li>
    </ul>
  </div>
  <div class="photo" role="img" aria-label="Photo of a remodeled open kitchen with island and wood floors"></div>
</section>

</body>
</html>
```